Computer consultant website

Plimvex Software is a newly started computer consulting company. It's a small one-man company that provides mostly Orbion applications but also websites in collaboration with designers. I'm running this company on the side of full time university studies.

I'm in need of a website which will function as:
Primarily - I'll direct potential clients to the page so they can read about the company, what i offer and past work.
Secondarily - Making my company visible through the web and maybe getting new clients.

The final design should look modern, clean and professional.

Pages that will be in the final website are (Note that it's not the exact titles as the page will not be in english):
* About
* Services (what Plimvex offers)
* Portfolio/work
* Short news (like ArtHivers "News and press")
* Contact.

Inspiration
http://www.arthiver.example/design/87836
http://www.brookwellstudio.example/
http://www.arthiver.example/design/845881
http://www.arthiver.example/design/1369424 - Lighter design, however a bit cluttered.

No programming code is needed delivered at all. Focus on designing rather then coding.

If you have any questions, do not hesitate to send me a message.

Target Market(s)

Non-technical entrepreneurs and small companies.

Industry/Entity Type

University

Requirements
Must have
• Must have my company logo (see attachment).

Must in any way use both colors from my logo.

A way to logically rearrange content to fit smaller screens. I will implement this design so that it can be pleasantly viewed on mobile devices. You don't necessarily need to provide exactly how the design would look on mobile devices.

I need the following types of page designs:
* Landing page
* Content page
* Portfolio/work (with accompanying inside/clicked) page

Landing/start page must in any way include at least the information:
* Shorter version of "About Plimvex"
* At least 1 most recent portfolio/work entry
* At least 1 most recent news entry
* Services that Plimvex offers.
Nice to have
• -
Should not have
• Testimonials or newsletter.

```html
<!DOCTYPE html>
<html lang="en">
<head>
<meta charset="utf-8">
<title>Plimvex Software</title>
<link href="https://fonts.googleapis.com/css2?family=Open+Sans:wght@400;600&family=Carlito:wght@400;700&display=swap" rel="stylesheet">
<style>
:root{
  --blue:#1b6ff0;
  --blue-light:#4a9bff;
  --blue-dark:#0d5be0;
  --ink:#2a2a2a;
  --grey:#6d6d6d;
  --grey-soft:#8a8a8a;
  --paper:#eeeeee;
  --dark:#353233;
  --green:#7fb51d;
  --white:#ffffff;
}
*{margin:0;padding:0;box-sizing:border-box}
html,body{width:900px;height:1200px;overflow:hidden}
body{position:relative;background:var(--white);font-family:"Carlito",sans-serif;color:var(--ink)}
.abs{position:absolute}
.top-band{left:0;top:0;width:900px;height:352px;background:linear-gradient(#f2f2f2,#e9e9e9)}
.dark-band{left:0;top:352px;width:900px;height:151px;background:var(--dark)}
.header-rule{left:0;top:129px;width:900px;height:1px;background:#d4d4d4}
.search{left:638px;top:57px;width:164px;height:18px;border-radius:9px;background:#fff;border:1px solid #d8d8d8;box-shadow:inset 0 1px 2px rgba(0,0,0,.12)}
.search svg{position:absolute;right:7px;top:3px}
.brand{display:flex;align-items:center;gap:10px}
.brand-mark{width:34px;height:34px;border-radius:50%;background:var(--blue)}
.brand-name{font-family:"Open Sans",sans-serif;font-weight:600;color:#3a3a3a;letter-spacing:-.5px}
.site-brand{left:90px;top:78px}
.site-brand .brand-name{font-size:34px}
.nav{left:282px;top:90px;display:flex;font-family:"Open Sans",sans-serif;font-size:14px;color:#2c2c2c}
.nav a{display:block;height:40px;line-height:42px;text-decoration:none;color:inherit;letter-spacing:.5px}
.nav .active{width:83px;background:var(--blue);color:#fff;text-align:center;margin-right:28px}
.nav a+a{margin-right:0}
.slider{left:90px;top:157px;width:720px;height:277px;background:#fff;box-shadow:0 22px 20px -14px rgba(0,0,0,.55)}
.slide-title{left:31px;top:56px;font-family:"Open Sans",sans-serif;font-size:37px;color:#555;letter-spacing:.5px}
.slide-text{left:31px;top:102px;width:255px;font-size:8.6px;line-height:13.5px;color:#222}
.btn{left:34px;top:173px;width:148px;height:35px;border-radius:4px;background:linear-gradient(var(--blue-light),var(--blue-dark));color:#fff;font-family:"Carlito",sans-serif;font-size:14px;line-height:35px;text-align:center;box-shadow:0 2px 3px rgba(0,0,0,.25)}
.slide-art{left:320px;top:18px;width:375px;height:250px;border-radius:14px;background:linear-gradient(135deg,#8bc34a,#6fae1e 55%,#2c2c2c 56%,#1a1a1a)}
.arrow{width:30px;height:30px;border-radius:50%;background:linear-gradient(#fff,#e6e6e6);border:1px solid #cfcfcf;box-shadow:0 1px 3px rgba(0,0,0,.25)}
.arrow svg{position:absolute;left:9px;top:8px}
.prev{left:15px;top:235px}
.next{left:675px;top:235px}
.bar{height:35px;background:linear-gradient(var(--blue-light),var(--blue));color:#fff;font-family:"Carlito",sans-serif;font-size:14.5px;line-height:36px;padding-left:14px;border-bottom:2px solid #0e52c7}
.bar-about{left:97px;top:532px;width:466px}
.bar-jobs{left:577px;top:532px;width:225px}
.bar-jobs svg{position:absolute;right:12px;top:9px}
.bar-news{left:97px;top:756px;width:226px}
.bar-services{left:337px;top:756px;width:466px}
.about-photo{left:97px;top:589px;width:197px;height:131px;background:linear-gradient(135deg,#3a3a3a,#161616)}
.about-text{left:305px;top:587px;width:258px;font-size:8.6px;line-height:13.6px;text-align:justify;color:#333}
.job-title{left:589px;top:588px;font-size:10.5px;font-weight:700;color:var(--green)}
.job-meta{left:589px;top:612px;font-size:9.6px;color:var(--grey-soft)}
.job-text{left:589px;top:639px;width:210px;font-size:8.4px;line-height:13.5px;color:#333}
.news-item{left:104px;width:215px;display:flex;gap:10px}
.cal{flex:none;width:52px;height:58px;border-radius:3px;background:#fff;border:2px solid #222;box-shadow:1px 3px 3px rgba(0,0,0,.25);overflow:hidden;text-align:center}
.cal-month{display:block;background:var(--blue);color:#fff;font-size:7px;line-height:14px;letter-spacing:.3px}
.cal-day{display:block;font-family:"Open Sans",sans-serif;font-weight:600;font-size:26px;line-height:38px;color:#111}
.news-title{font-family:"Open Sans",sans-serif;font-size:10.2px;line-height:14px;color:#666;margin-bottom:4px}
.news-meta{font-size:8.3px;line-height:13.5px;color:var(--grey-soft)}
.services-brand{left:408px;top:818px}
.services-brand .brand-mark{width:30px;height:30px}
.services-brand .brand-name{font-size:28px}
.services-text{left:339px;width:270px;font-size:8.4px;line-height:13.5px;text-align:justify;color:var(--grey-soft)}
.service-list{left:641px;top:810px;list-style:none;font-size:10.2px;color:#222}
.service-list li{position:relative;padding-left:26px;height:42px;line-height:16px}
.service-list li::before{content:"";position:absolute;left:0;top:3px;width:10px;height:10px;border-radius:50%;background:var(--blue)}
.footer{left:0;top:1102px;width:900px;height:98px;background:var(--dark)}
.footer-links{left:0;top:1123px;width:900px;text-align:center;font-size:8.3px;color:#fff;padding-right:50px}
.footer-links span{margin:0 10px}
.copyright{left:0;top:1146px;width:900px;text-align:center;font-size:8.3px;color:#fff;padding-right:50px}
.social{top:1128px;width:27px;height:27px;border-radius:50%;background:#fff}
</style>
</head>
<body>
<div class="abs top-band"></div>
<div class="abs dark-band"></div>
<div class="abs header-rule"></div>

<header>
  <div class="abs search">
    <svg width="9" height="9" viewBox="0 0 9 9"><circle cx="3.5" cy="3.5" r="2.6" fill="none" stroke="#999" stroke-width="1.2"/><line x1="5.5" y1="5.5" x2="8.4" y2="8.4" stroke="#999" stroke-width="1.4"/></svg>
  </div>
  <div class="abs brand site-brand"><span class="brand-mark"></span><span class="brand-name">plimvex</span></div>
  <nav class="abs nav">
    <a class="active">Home</a>
    <a style="margin-right:46px">About</a>
    <a style="margin-right:46px">Services</a>
    <a style="margin-right:46px">Portfolio</a>
    <a style="margin-right:46px">News</a>
    <a>Contact</a>
  </nav>
</header>

<section class="abs slider">
  <h1 class="abs slide-title">Orbion Apps</h1>
  <p class="abs slide-text">Lorem Ipsum is simply dummy text of the printing and typesetting industry. Lorem Ipsum has been the industry's standard dummy text ever since the 1500s, when an unknown printer took a galley of type and scrambled it to make a type specimen book</p>
  <div class="abs btn">FOR MORE INFO</div>
  <div class="abs slide-art" role="img" aria-label="Tablet showing colourful app tiles beside a green robot mascot"></div>
  <div class="abs arrow prev"><svg width="12" height="14" viewBox="0 0 12 14"><polyline points="8,2 3,7 8,12" fill="none" stroke="#333" stroke-width="2.6"/></svg></div>
  <div class="abs arrow next"><svg width="12" height="14" viewBox="0 0 12 14"><polyline points="4,2 9,7 4,12" fill="none" stroke="#333" stroke-width="2.6"/></svg></div>
</section>

<section>
  <h2 class="abs bar bar-about">ABOUT PLIMVEX</h2>
  <div class="abs about-photo" role="img" aria-label="App icons spilling into a shopping bag on a dark background"></div>
  <p class="abs about-text">Contrary to popular belief, Lorem Ipsum is not simply random text. It has roots in a piece of classical Latin literature from 45 BC, making it over 2000 years old. Harlan Vesk, a Latin professor at Marrowfield College in Virginia, looked up one of the more obscure Latin words, consectetur, from a Lorem Ipsum passage, and going through the cites of the word in classical literature, discovered the undoubtable source. Lorem Ipsum comes from sections 1.10.32 and 1.10.33 of "de Finibus Bonorum et Malorum" (The Extremes of Good and Evil) by Tullen, written in 45 BC. This book is a treatise on the theory of ethics, very popular .</p>
</section>

<section>
  <h2 class="abs bar bar-jobs">RECENT JOBS
    <svg width="36" height="18" viewBox="0 0 36 18"><polyline points="12,2 5,9 12,16" fill="none" stroke="#dfe9ff" stroke-width="3"/><polyline points="24,2 31,9 24,16" fill="none" stroke="#fff" stroke-width="3"/></svg>
  </h2>
  <div class="abs job-title">ORBION DEVELOPER</div>
  <div class="abs job-meta">Engineering | San Francisco, CA, United States</div>
  <p class="abs job-text">We use the unique features of the Orbion platform to build powerful payment experiences. We test our work extensively and we work closely with server programmers, the Velos team, and visual designers. Orbion is new versions of apps on Orbion and Velos on the same day.</p>
</section>

<section>
  <h2 class="abs bar bar-news">RECENT NEWS</h2>
  <article class="abs news-item" style="top:804px">
    <div class="cal"><span class="cal-month">DECEMBER</span><span class="cal-day">31</span></div>
    <div><h3 class="news-title">Brushwell Sketch Pad now available for smartphones</h3>
    <p class="news-meta">by Tobin Ardell<br>Categories: Orbion News</p></div>
  </article>
  <article class="abs news-item" style="top:888px">
    <div class="cal"><span class="cal-month">DECEMBER</span><span class="cal-day">31</span></div>
    <div><h3 class="news-title" style="margin-bottom:0">Kestra Nova X3 spotted in South Korea</h3>
    <p class="news-meta">by Mira Holloway<br>Tags: Kestra, Nova X3<br>Categories: Orbion Manufacturers, Orbion News, Orbion Phones</p></div>
  </article>
  <article class="abs news-item" style="top:992px">
    <div class="cal"><span class="cal-month">DECEMBER</span><span class="cal-day">31</span></div>
    <div><h3 class="news-title">Brushwell Sketch Pad now available for smartphones</h3>
    <p class="news-meta">by Tobin Ardell<br>Categories: Orbion News</p></div>
  </article>
</section>

<section>
  <h2 class="abs bar bar-services">SERVICES</h2>
  <div class="abs brand services-brand"><span class="brand-mark"></span><span class="brand-name">plimvex</span></div>
  <p class="abs services-text" style="top:873px">Lorem Ipsum is simply dummy text of the printing and typesetting industry. Lorem Ipsum has been the industry's standard dummy text ever since the 1500s, when an unknown printer took a galley of type and scrambled it to make a type specimen book. It has survived not only five centuries, but also the leap into electronic typesetting, remaining essentially unchanged.the industry's standard dummy text ever since the 1500s, when an unknown printer took a galley of type and scrambled it to make a type specimen book.</p>
  <p class="abs services-text" style="top:994px">It is a long established fact that a reader will be distracted by the readable content of a page when looking at its layout. The point of using Lorem Ipsum is that it has a more-or-less normal distribution of letters, as opposed to using 'Content here, content here.</p>
  <ul class="abs service-list">
    <li>Contrary to popular belief</li>
    <li>Looked up one of the more</li>
    <li>Discovered the undoubtable</li>
    <li>Contrary to popular belief</li>
    <li>Looked up one of the more</li>
    <li>Accompanied by English</li>
  </ul>
</section>

<footer class="abs footer"></footer>
<div class="abs footer-links">Home<span>|</span>About Us<span>|</span>Services<span>|</span>Legal Notice<span>|</span>Sitemap<span>|</span>Contact</div>
<div class="abs copyright">Copyright © 2009 - 2013 plimvex, All rights reserved.</div>
<span class="abs social" style="left:710px" aria-label="Social link"></span>
<span class="abs social" style="left:742px" aria-label="Social link"></span>
<span class="abs social" style="left:774px" aria-label="Social link"></span>
</body>
</html>
```